Business Card for a mobile physiotherapy company

I need a layout for a business card for a mobile physiotherapy company.
Slogan is "Mobile Physiotherapy - Your Road To Recovery"
Phone number is 867-555-0142
Email VardenTherapy@postnest.ca (subject to change with website)
Website www.VardenTherapy.ca
My name and credentials: Luke Varden Luke Varden, BSc(kin), MPT, CAFCI, IMS
Information maybe included: Direct Billing, Services including Physiotherapy, IMS, acupuncture
Maybe include facebook and instagram logos
One side with the logo clean and sharp
Other side with details, try not to look too busy, keep everything concise

```html
<!DOCTYPE html>
<html lang="en">
<head>
<meta charset="utf-8">
<title>Varden Therapy – Business Card</title>
<link rel="stylesheet" href="https://fonts.googleapis.com/css2?family=Lato:wght@400;700&family=Roboto:wght@400&display=swap">
<style>
  :root {
    --navy: #2b4a7a;
    --navy-deep: #24436f;
    --teal: #1d5e55;
    --paper: #ffffff;
    --stage: #a9a9a9;
    --ink-soft: #eef2f8;
  }
  * { box-sizing: border-box; margin: 0; padding: 0; }
  html, body { width: 1200px; height: 930px; overflow: hidden; }
  body {
    background: var(--stage);
    position: relative;
    font-family: "Lato", sans-serif;
  }
  .card {
    position: absolute;
    width: 560px;
    height: 320px;
    border-radius: 22px;
    box-shadow: 0 10px 24px rgba(0,0,0,0.28);
    overflow: hidden;
  }
  .card-front {
    left: 70px; top: 80px;
    background: linear-gradient(135deg, var(--navy) 0%, var(--navy-deep) 100%);
    color: var(--ink-soft);
  }
  .card-back {
    left: 570px; top: 520px;
    background: var(--paper);
  }
  .brand {
    position: absolute;
    display: flex;
    align-items: center;
    gap: 12px;
    font-family: "Lato", sans-serif;
    font-weight: 700;
    letter-spacing: 0.04em;
    white-space: nowrap;
  }
  .brand-mark { display: block; flex: none; }
  .card-front .brand {
    left: 50%; top: 112px;
    transform: translateX(-50%);
    font-size: 40px;
    color: var(--paper);
  }
  .card-front .brand-mark { width: 22px; height: 22px; background: var(--paper); }
  .slogan {
    position: absolute;
    left: 0; right: 0; bottom: 34px;
    text-align: center;
    font-size: 17px;
    color: var(--ink-soft);
  }
  .card-back .brand {
    right: 30px; top: 130px;
    font-size: 30px;
    color: var(--navy);
  }
  .card-back .brand-mark { width: 16px; height: 16px; background: var(--navy); }
  .identity { position: absolute; left: 34px; top: 44px; width: 240px; }
  .identity-name {
    font-family: "Roboto", sans-serif;
    font-weight: 400;
    font-size: 25px;
    line-height: 1.15;
    color: var(--navy);
    white-space: nowrap;
  }
  .identity-services {
    margin-top: 8px;
    font-size: 14px;
    line-height: 1.35;
    color: var(--teal);
    white-space: nowrap;
  }
  .contact {
    position: absolute;
    left: 34px; bottom: 36px;
    list-style: none;
    font-size: 15px;
    line-height: 1.6;
    color: var(--teal);
  }
  .contact li { white-space: nowrap; }
  .contact-label {
    display: inline-block;
    width: 28px;
    color: var(--navy);
    white-space: nowrap;
  }
</style>
</head>
<body>
  <section class="card card-front" aria-label="Card front">
    <div class="brand"><span class="brand-mark"></span>Varden Therapy</div>
    <p class="slogan">Mobile Physiotherapy - Your Road To Recovery</p>
  </section>

  <section class="card card-back" aria-label="Card back">
    <div class="identity">
      <h1 class="identity-name">Luke Varden, BSc(kin),<br>MPT, CAFCI, IMS</h1>
      <p class="identity-services">Direct Billing, Services including<br>Physiotherapy, IMS, acupuncture</p>
    </div>
    <div class="brand"><span class="brand-mark"></span>Varden Therapy</div>
    <ul class="contact">
      <li><span class="contact-label">P :</span>867-555-0142</li>
      <li><span class="contact-label">E :</span>VardenTherapy@postnest.ca</li>
      <li><span class="contact-label">W :</span>www.VardenTherapy.ca</li>
    </ul>
  </section>
</body>
</html>
```